WEBSITE & LOGO for MEDICAL CILINC

BRAND NAME ( LUMORA) Medical clinic for intravenous (IV) vitamin hydration and wellness therapy. range of signature infusions and boosters are targeted at preventative health and wellness – essentially replenishing your body with the fluids and vitamins it needs to be in tip-top condition.

Blood testing
laboratory analysis
IV therapy
IV infusion drips
phlebotomy services
nurses for Home care services
Patient repatriation services to their countries
Hire of medical equipments including beds and wheel chairs

www.quellsa.com
www.tovexclinic.com
http://pickaflask.co.uk

All adults
18+ women and men.

No black color in the background
DNA double helix image should to be implemented in the design and logo.
the website should be easy to be used so the clients can add to the shopping cart
- select treatment or drips
- supplement
- book nurses
- book home visit
- book nurse for international home care journey

Colors
86cae7
33b8a4
e4daeb
f9d9e8
fefafc
fbd2d3
eee9f4
85acd3
0455a3

Requirements
Must have
• DNA Double helix in Java animation
injection icon for IV injection
Infusion Icon Bag for IV infusion
Analysis icon
phlebotomy services icon
Patient repatriation services icon
Hire of medical equipments icon

light background and water blue menu and buttons with highlights
Nice to have
• dynamic website where
IV injections scroll from side to side
IV infusion scroll from side to side.

```html
<!DOCTYPE html>
<html lang="en">
<head>
<meta charset="utf-8">
<title>LUMORA – Home page layouts</title>
<link href="https://fonts.googleapis.com/css2?family=Roboto:wght@400;500;700&family=Lato:wght@400;700&display=swap" rel="stylesheet">
<style>
:root{
  --stage:#f1f1f1;
  --ink:#222;
  --body:#444;
  --muted:#777;
  --royal:#0a4f9e;
  --royal-dark:#0b5aa8;
  --sky:#1aa0e0;
  --teal:#33b8a4;
  --teal-deep:#1f9a9a;
  --pink:#fbc3c7;
  --green:#6cc43a;
  --white:#fff;
  --line:#d6d6d6;
}
*{box-sizing:border-box;margin:0;padding:0}
html,body{width:727px;height:1200px;overflow:hidden;background:var(--stage)}
body{position:relative;font-family:"Roboto",Arial,sans-serif;color:var(--body)}

.page{position:absolute;top:29px;width:319px;background:var(--white);box-shadow:0 0 2px rgba(0,0,0,.35);display:flex;flex-direction:column;overflow:hidden}
.page--waved{left:22px}
.page--straight{left:378px}
.block{position:relative;height:var(--h);flex:none}

/* header */
.site-header{background:var(--white)}
.brand{position:absolute;display:flex;align-items:center;gap:3px;font-weight:700;font-size:6.5px;color:var(--royal);letter-spacing:.1px}
.brand__dot{width:9px;height:9px;border-radius:50%;background:var(--teal)}
.site-header .brand{left:31px;top:12px}
.nav{position:absolute;left:86px;top:14px;display:flex;gap:8px;font-size:3.9px;color:#333}
.nav__item--active{color:var(--royal)}
.btn-visit{position:absolute;left:222px;top:9px;width:47px;height:14px;background:var(--royal);color:#fff;font-size:4.1px;font-weight:500;display:flex;align-items:center;justify-content:center;border-radius:1px}
.cart{position:absolute;left:274px;top:14px;font-size:4px;color:var(--sky);display:flex;align-items:center;gap:1px}
.cart svg{width:6px;height:5px}

/* hero */
.hero__photo{position:absolute;inset:0;background:
  radial-gradient(ellipse at 80% 70%,rgba(255,170,80,.85),transparent 45%),
  radial-gradient(ellipse at 30% 40%,rgba(230,160,220,.7),transparent 55%),
  linear-gradient(120deg,#4b3a9c 0%,#7b6ac9 35%,#c98bb7 60%,#e5a26a 80%,#5b4fae 100%)}
.hero__content{position:absolute;left:0;right:0;top:40px;text-align:center;color:#fff}
.hero__title{font-size:19px;font-weight:700;letter-spacing:.5px;text-shadow:0 1px 2px rgba(0,0,0,.5)}
.hero__lead{margin:7px auto 0;width:205px;font-size:6px;line-height:10px;font-weight:500;text-shadow:0 1px 1px rgba(0,0,0,.6)}
.btn-journey{display:inline-block;margin-top:6px;width:151px;height:15px;line-height:15px;background:var(--royal);color:#fff;font-size:4.2px;font-weight:500;border-radius:1px}
.dots{position:absolute;left:0;right:0;display:flex;justify-content:center;gap:3px}
.dots i{width:3px;height:3px;border-radius:50%;background:#fff;opacity:.8}
.dots i.on{background:var(--royal);opacity:1}
.hero__curve{position:absolute;left:0;bottom:-1px;width:319px;height:17px}

/* welcome */
.welcome{text-align:center}
.section-title{font-size:10px;font-weight:700;color:var(--ink);letter-spacing:.2px}
.section-title em{font-style:normal;color:var(--teal)}
.section-title--light{color:#fff}
.welcome__text{width:244px;margin:10px auto 0;font-size:3.9px;line-height:8.9px;color:var(--body)}
.actions{display:flex;justify-content:center;gap:9px;margin-top:10px}
.btn{height:14px;padding:0 4px;display:flex;align-items:center;font-size:4.6px;font-weight:700;color:#fff;border-radius:1px}
.btn--royal{background:var(--royal);width:38px;justify-content:center}
.btn--teal{background:var(--teal);width:47px;justify-content:center}

/* services */
.band{color:#fff;text-align:center}
.band__bg{position:absolute;inset:0}
.band__bg--services{background:linear-gradient(180deg,#0c6bb8 0%,#1a8fc0 55%,#2aa6a8 100%)}
.band__bg--blog{background:linear-gradient(180deg,#0d5fb2 0%,#1b86c2 55%,#2aa8ac 100%)}
.band__edge{position:absolute;left:0;width:319px;height:20px}
.band__inner{position:relative}
.band__lead{width:210px;margin:6px auto 0;font-size:4.1px;line-height:8.6px}
.cards{display:flex;justify-content:center;gap:14px;margin-top:14px}
.service{width:77px;height:69px;background:#fff;border-radius:1px;box-shadow:0 1px 2px rgba(0,0,0,.2);padding-top:5px;color:var(--body)}
.service__icon{width:28px;height:28px;margin:0 auto;display:block}
.service__name{font-size:5.3px;font-weight:500;color:#555;margin-top:3px;letter-spacing:.1px}
.service__text{font-size:3.6px;line-height:7px;margin-top:2px;padding:0 4px}

/* testimonials */
.testimonials{text-align:center}
.quote{position:absolute;font-family:"Roboto",Arial,sans-serif;font-weight:700;font-size:58px;line-height:1;color:#d0d0d0}
.avatar{width:25px;height:25px;border-radius:50%;border:1px solid var(--teal);margin:0 auto;background:radial-gradient(circle at 50% 35%,#c9a38a 0 28%,#6f6a66 30% 60%,#9aa5a5 62%)}
.testimonial__text{width:188px;margin:10px auto 0;font-family:"Lato",Arial,sans-serif;font-size:4.1px;line-height:8.2px;color:#888}
.testimonial__author{font-family:"Lato",Arial,sans-serif;font-size:4.1px;color:#777;margin-top:6px}
.arrow{position:absolute;width:9px;height:9px;border-radius:50%;border:.6px solid #999;display:flex;align-items:center;justify-content:center;font-size:5px;color:#666}

/* blog */
.posts{display:flex;justify-content:center;gap:9px;margin-top:14px}
.post{width:80px;height:97px;background:#fff;position:relative;color:var(--body)}
.post__photo{height:48px;display:block}
.post__photo--1{background:linear-gradient(135deg,#cfdbe8,#8ba9c9 50%,#e6e9ef)}
.post__photo--2{background:linear-gradient(135deg,#5a6f88,#c8d3de 45%,#f0b06a 75%,#6a7d93)}
.post__photo--3{background:linear-gradient(135deg,#f3e6d8,#e8b26a 45%,#d7d0c8)}
.post__date{position:absolute;right:3px;top:3px;width:14px;height:33px;background:#fff;border-radius:7px;text-align:center}
.post__day{display:block;background:var(--sky);color:#fff;border-radius:7px 7px 0 0;font-size:5px;line-height:9px}
.post__month{display:block;font-size:2.6px;line-height:3.3px;color:var(--sky);margin-top:1px}
.post__by{display:flex;align-items:center;justify-content:center;gap:2px;font-size:4.2px;font-weight:700;color:#333;margin-top:5px}
.post__by i{width:7px;height:7px;border-radius:50%;background:var(--sky)}
.post__text{font-size:3.7px;line-height:6.8px;margin-top:2px;padding:0 4px}
.post__more{position:absolute;left:50%;bottom:-4px;transform:translateX(-50%);width:36px;height:9px;border-radius:5px;background:#1e90d6;border:.6px solid #fff;color:#fff;font-size:3.7px;line-height:8px}

/* newsletter */
.newsletter{text-align:center}
.newsletter__text{width:230px;margin:8px auto 0;font-size:4.7px;line-height:8.6px;color:#333}
.subscribe{display:flex;justify-content:center;align-items:center;gap:4px;margin-top:10px}
.subscribe__field{width:85px;height:15px;border:.7px solid #bbb;border-radius:8px;display:flex;align-items:center;justify-content:space-between;padding:0 8px 0 9px;font-family:"Lato",Arial,sans-serif;font-size:4.6px;color:#444}
.subscribe__field svg{width:7px;height:6px}
.subscribe__btn{width:45px;height:13px;border-radius:7px;background:var(--royal);color:#fff;font-size:4.9px;font-weight:500;display:flex;align-items:center;justify-content:center}

/* footer */
.footer{background:linear-gradient(180deg,#0e5ea9 0%,#1672b2 55%,#1f8ea8 100%);color:#fff}
.footer .brand{color:#fff}
.footer__about{position:absolute;font-size:3.6px;line-height:6.8px;width:82px;color:#e4eef7}
.footer__col{position:absolute}
.footer__head{font-size:5px;font-weight:700;letter-spacing:.1px}
.footer__links{list-style:none;margin-top:6px;font-size:3.6px;line-height:8.6px;color:#e4eef7}
.footer__contact{margin-top:6px;font-size:4.9px;line-height:11.5px}
.footer__contact b{font-weight:700}
.social{display:flex;gap:5px;margin-top:6px}
.social i{width:10px;height:10px;border-radius:50%;border:.7px solid #fff}
.footer__legal{position:absolute;left:0;right:0;text-align:center;font-family:"Lato",Arial,sans-serif;font-size:3.4px;color:#e4eef7}
</style>
</head>
<body>

<!-- ================= Waved variant ================= -->
<main class="page page--waved">
  <header class="block site-header" style="--h:30px">
    <div class="brand"><span class="brand__dot"></span>LUMORA</div>
    <nav class="nav"><span class="nav__item--active">HOME</span><span>ABOUT US</span><span>SERVICES</span><span>BLOG</span><span>CONTACT US</span></nav>
    <div class="btn-visit">BOOK HOME VISIT</div>
    <div class="cart"><svg viewBox="0 0 12 10"><path d="M0 1h2l2 6h6l1.5-4.5H3" fill="none" stroke="#1aa0e0" stroke-width="1.3"/><circle cx="5" cy="9" r="1" fill="#1aa0e0"/><circle cx="9" cy="9" r="1" fill="#1aa0e0"/></svg>Cart</div>
  </header>

  <section class="block hero" style="--h:151px">
    <div class="hero__photo" role="img" aria-label="Glowing DNA double helix in violet and amber light"></div>
    <div class="hero__content">
      <h1 class="hero__title">LUMORA</h1>
      <p class="hero__lead">Sed ut perspiciatis unde omnis iste natus error sit voluptatem accusantium doloremque laudantium.</p>
      <span class="btn-journey">BOOK NURSE FOR INTERNATIONAL HOME CARE JOURNEY</span>
    </div>
    <div class="dots" style="top:135px"><i></i><i></i><i class="on"></i></div>
    <svg class="hero__curve" viewBox="0 0 319 17" preserveAspectRatio="none"><path d="M0 4Q160 26 319 4V17H0Z" fill="#fff"/><path d="M0 4Q160 26 319 4" fill="none" stroke="#6cc43a" stroke-width="1.6"/></svg>
  </section>

  <section class="block welcome" style="--h:156px">
    <h2 class="section-title" style="padding-top:20px">WELCOME <em>TO LUMORA</em></h2>
    <p class="welcome__text">Sed ut perspiciatis unde omnis iste natus error sit voluptatem accusantium doloremque laudantium, totam rem aperiam, eaque ipsa quae ab illo inventore veritatis et quasi architecto beatae vitae dicta sunt explicabo. Nemo enim ipsam voluptatem quia voluptas sit aspernatur aut odit aut fugit, sed quia consequuntur magni dolores eos qui ratione voluptatem sequi nesciunt. Neque porro quisquam est, qui dolorem ipsum quia dolor sit amet, consectetur, adipisci velit, sed quia non numquam eius modi tempora incidunt ut labore et dolore magnam aliquam quaerat voluptatem. Ut enim ad minima veniam, quis nostrum exercitationem ullam corporis suscipit laboriosam, nisi ut aliquid ex ea commodi consequatur? Quis autem vel eum iure reprehenderit qui in ea voluptate velit esse quam nihil molestiae consequatur.</p>
    <div class="actions"><span class="btn btn--royal">READ MORE</span><span class="btn btn--teal">BOOK NURSES</span></div>
  </section>

  <section class="block band services" style="--h:187px">
    <div class="band__bg band__bg--services" role="img" aria-label="Soft blue and teal backdrop of DNA strands"></div>
    <svg class="band__edge" style="top:0" viewBox="0 0 319 20" preserveAspectRatio="none"><path d="M0 0H319V16Q200 -4 0 16Z" fill="#fff"/><path d="M0 16Q200 -4 319 16V8Q200 -6 0 14Z" fill="#fbc3c7"/></svg>
    <div class="band__inner" style="padding-top:25px">
      <h2 class="section-title section-title--light">OUR SERVICES</h2>
      <p class="band__lead">sed ut perspiciatis unde omnis iste natus error sit voluptatem accusantium doloremque laudantium, totam rem aperiam, eaque ipsa quae ab illo inventore veritatis et quasi .</p>
      <div class="cards">
        <article class="service"><svg class="service__icon" viewBox="0 0 28 28"><circle cx="14" cy="14" r="13" fill="none" stroke="#0a4f9e" stroke-width="1.2"/><circle cx="14" cy="14" r="11" fill="#1aa0e0"/><path d="M14 7c3 4 4 6 4 8a4 4 0 0 1-8 0c0-2 1-4 4-8z" fill="none" stroke="#fff" stroke-width="1"/></svg><h3 class="service__name">BLOOD TESTING</h3><p class="service__text">At vero eos et accusamus et iusto odio dignissimos ducimus qui</p></article>
        <article class="service"><svg class="service__icon" viewBox="0 0 28 28"><circle cx="14" cy="14" r="13" fill="none" stroke="#0a4f9e" stroke-width="1.2"/><circle cx="14" cy="14" r="11" fill="#1aa0e0"/><path d="M12 7h4M13 7v5l-4 7h10l-4-7V7" fill="none" stroke="#fff" stroke-width="1"/></svg><h3 class="service__name">LABORATORY ANALYSIS</h3><p class="service__text">At vero eos et accusamus et iusto odio dignissimos ducimus qui</p></article>
        <article class="service"><svg class="service__icon" viewBox="0 0 28 28"><circle cx="14" cy="14" r="13" fill="none" stroke="#0a4f9e" stroke-width="1.2"/><circle cx="14" cy="14" r="11" fill="#1aa0e0"/><rect x="10" y="7" width="8" height="10" rx="2" fill="none" stroke="#fff" stroke-width="1"/><path d="M14 17v4" stroke="#fff" stroke-width="1"/></svg><h3 class="service__name">IV THERAPY</h3><p class="service__text">At vero eos et accusamus et iusto odio dignissimos ducimus qui</p></article>
      </div>
      <div class="dots" style="position:static;margin-top:21px"><i></i><i></i><i></i></div>
    </div>
    <svg class="band__edge" style="bottom:0" viewBox="0 0 319 20" preserveAspectRatio="none"><path d="M0 4Q120 20 319 4V20H0Z" fill="#fff"/><path d="M0 0V10Q120 20 319 2V0Q120 14 0 0Z" fill="#fbc3c7"/></svg>
  </section>

  <section class="block testimonials" style="--h:149px">
    <h2 class="section-title" style="padding-top:24px">TESTIMONIALS</h2>
    <span class="quote" style="left:42px;top:40px">“</span>
    <span class="quote" style="left:251px;top:94px">”</span>
    <div style="margin-top:13px"><div class="avatar" role="img" aria-label="Client portrait"></div></div>
    <p class="testimonial__text">Sed ut perspiciatis unde omnis iste natus error sit voluptatem accusantium doloremque laudantium, totam rem aperiam, eaque ipsa quae ab illo inventore veritatis et quasi architecto beatae vitae dicta sunt explicabo. Nemo enim ipsam voluptatem quia voluptas .</p>
    <p class="testimonial__author">-By Author Name</p>
    <span class="arrow" style="left:18px;top:83px">←</span>
    <span class="arrow" style="left:289px;top:83px">→</span>
  </section>

  <section class="block band blog" style="--h:185px">
    <div class="band__bg band__bg--blog" role="img" aria-label="Blue and teal backdrop of DNA strands"></div>
    <svg class="band__edge" style="top:0" viewBox="0 0 319 20" preserveAspectRatio="none"><path d="M0 0H319V6Q160 -2 0 16Z" fill="#fff"/><path d="M0 16Q160 -2 319 6V14Q160 4 0 18Z" fill="#fbc3c7"/></svg>
    <div class="band__inner" style="padding-top:20px">
      <h2 class="section-title section-title--light">LATEST &nbsp;BLOG</h2>
      <div class="posts">
        <article class="post"><div class="post__photo post__photo--1" role="img" aria-label="Gloved hand holding a blood sample tube"></div><div class="post__date"><span class="post__day">31</span><span class="post__month">J<br>U<br>L<br>Y</span></div><p class="post__by"><i></i>BY ADMIN</p><p class="post__text">At vero eos et accusamus et iusto odio dignissimos ducimus qui blanditiis praesentium .</p><span class="post__more">READ MORE</span></article>
        <article class="post"><div class="post__photo post__photo--2" role="img" aria-label="Laboratory microscope close-up"></div><div class="post__date"><span class="post__day">31</span><span class="post__month">J<br>U<br>L<br>Y</span></div><p class="post__by"><i></i>BY ADMIN</p><p class="post__text">At vero eos et accusamus et iusto odio dignissimos ducimus qui blanditiis praesentium .</p><span class="post__more">READ MORE</span></article>
        <article class="post"><div class="post__photo post__photo--3" role="img" aria-label="Therapist treating a patient's leg"></div><div class="post__date"><span class="post__day">31</span><span class="post__month">J<br>U<br>L<br>Y</span></div><p class="post__by"><i></i>BY ADMIN</p><p class="post__text">At vero eos et accusamus et iusto odio dignissimos ducimus qui blanditiis praesentium .</p><span class="post__more">READ MORE</span></article>
      </div>
      <div class="dots" style="position:static;margin-top:21px"><i></i><i class="on" style="background:#fff"></i></div>
    </div>
    <svg class="band__edge" style="bottom:0" viewBox="0 0 319 20" preserveAspectRatio="none"><path d="M0 12Q150 18 319 0V20H0Z" fill="#fff"/><path d="M0 4V14Q150 18 319 2V0Q150 14 0 4Z" fill="#fbc3c7"/></svg>
  </section>

  <section class="block newsletter" style="--h:127px">
    <h2 class="section-title" style="padding-top:33px">JOIN THE <em>NEWSLETTER</em></h2>
    <p class="newsletter__text">Sed ut perspiciatis unde omnis iste natus error sit voluptatem accusantium doloremque laudantium, totam rem aperiam, eaque ipsa quae ab illo inventore veritatis et quasi architecto.</p>
    <div class="subscribe"><div class="subscribe__field">Enter your Email<svg viewBox="0 0 12 10"><path d="M0 5L12 0 9 10 6 6Z" fill="#222"/></svg></div><span class="subscribe__btn">SUBMIT</span></div>
  </section>

  <footer class="block footer" style="--h:127px">
    <svg class="band__edge" style="top:0" viewBox="0 0 319 20" preserveAspectRatio="none"><path d="M0 0H319V2Q150 0 0 14Z" fill="#fff"/><path d="M0 14Q150 0 319 2V4Q150 4 0 16Z" fill="#1aa0e0"/></svg>
    <div class="brand" style="left:26px;top:32px"><span class="brand__dot"></span>LUMORA</div>
    <p class="footer__about" style="left:26px;top:54px">Lorem ipsum dolor sit amet, consectetur adipiscing elit, sed do eiusmod tempor incididunt ut labore et dolore magna aliqua. Ut enim ad minim veniam,</p>
    <div class="footer__col" style="left:121px;top:35px"><h4 class="footer__head">QUICKLINK</h4><ul class="footer__links"><li>HOME</li><li>ABOUTUS</li><li>SERVICES</li><li>BLOG</li><li>CONTACT US</li></ul></div>
    <div class="footer__col" style="left:174px;top:35px"><h4 class="footer__head">CONTACT US</h4><div class="footer__contact"><b>555-014-2200</b><br>info@lumora.com<br><span style="line-height:6px;display:block">12 Marrow Lane,<br>Avelon 20410</span></div></div>
    <div class="footer__col" style="left:248px;top:35px"><h4 class="footer__head">FOLLOW US</h4><div class="social"><i></i><i></i><i></i></div></div>
    <p class="footer__legal" style="bottom:11px">Copyrights © 2020 Copyrights Company Name | All Rights Reserved</p>
  </footer>
</main>

<!-- ================= Straight variant ================= -->
<main class="page page--straight">
  <header class="block site-header" style="--h:32px">
    <div class="brand"><span class="brand__dot"></span>LUMORA</div>
    <nav class="nav"><span class="nav__item--active">HOME</span><span>ABOUT US</span><span>SERVICES</span><span>BLOG</span><span>CONTACT US</span></nav>
    <div class="btn-visit">BOOK HOME VISIT</div>
    <div class="cart"><svg viewBox="0 0 12 10"><path d="M0 1h2l2 6h6l1.5-4.5H3" fill="none" stroke="#1aa0e0" stroke-width="1.3"/><circle cx="5" cy="9" r="1" fill="#1aa0e0"/><circle cx="9" cy="9" r="1" fill="#1aa0e0"/></svg>Cart</div>
  </header>

  <section class="block hero" style="--h:148px">
    <div class="hero__photo" role="img" aria-label="Glowing DNA double helix in violet and amber light"></div>
    <div class="hero__content" style="top:37px">
      <h1 class="hero__title">LUMORA</h1>
      <p class="hero__lead">Sed ut perspiciatis unde omnis iste natus error sit voluptatem accusantium doloremque laudantium.</p>
      <span class="btn-journey">BOOK NURSE FOR INTERNATIONAL HOME CARE JOURNEY</span>
    </div>
    <div class="dots" style="top:138px"><i class="on"></i><i></i><i></i></div>
  </section>

  <section class="block welcome" style="--h:151px">
    <h2 class="section-title" style="padding-top:21px">WELCOME <em>TO LUMORA</em></h2>
    <p class="welcome__text">Sed ut perspiciatis unde omnis iste natus error sit voluptatem accusantium doloremque laudantium, totam rem aperiam, eaque ipsa quae ab illo inventore veritatis et quasi architecto beatae vitae dicta sunt explicabo. Nemo enim ipsam voluptatem quia voluptas sit aspernatur aut odit aut fugit, sed quia consequuntur magni dolores eos qui ratione voluptatem sequi nesciunt. Neque porro quisquam est, qui dolorem ipsum quia dolor sit amet, consectetur, adipisci velit, sed quia non numquam eius modi tempora incidunt ut labore et dolore magnam aliquam quaerat voluptatem. Ut enim ad minima veniam, quis nostrum exercitationem ullam corporis suscipit laboriosam, nisi ut aliquid ex ea commodi consequatur? Quis autem vel eum iure reprehenderit qui in ea voluptate velit esse quam nihil molestiae consequatur.</p>
    <div class="actions"><span class="btn btn--royal">READ MORE</span><span class="btn btn--teal">BOOK NURSES</span></div>
  </section>

  <section class="block band services" style="--h:165px">
    <div class="band__bg band__bg--services" role="img" aria-label="Blue and teal backdrop with blurred lab equipment"></div>
    <div class="band__inner" style="padding-top:17px">
      <h2 class="section-title section-title--light">OUR SERVICES</h2>
      <p class="band__lead">sed ut perspiciatis unde omnis iste natus error sit voluptatem accusantium doloremque laudantium, totam rem aperiam, eaque ipsa quae ab illo inventore veritatis et quasi .</p>
      <div class="cards" style="gap:14px;margin-top:14px">
        <article class="service"><svg class="service__icon" viewBox="0 0 28 28"><circle cx="14" cy="14" r="13" fill="none" stroke="#0a4f9e" stroke-width="1.2"/><circle cx="14" cy="14" r="11" fill="#1aa0e0"/><path d="M14 7c3 4 4 6 4 8a4 4 0 0 1-8 0c0-2 1-4 4-8z" fill="none" stroke="#fff" stroke-width="1"/></svg><h3 class="service__name">BLOOD TESTING</h3><p class="service__text">At vero eos et accusamus et iusto odio dignissimos ducimus qui</p></article>
        <article class="service"><svg class="service__icon" viewBox="0 0 28 28"><circle cx="14" cy="14" r="13" fill="none" stroke="#0a4f9e" stroke-width="1.2"/><circle cx="14" cy="14" r="11" fill="#1aa0e0"/><path d="M12 7h4M13 7v5l-4 7h10l-4-7V7" fill="none" stroke="#fff" stroke-width="1"/></svg><h3 class="service__name">LABORATORY ANALYSIS</h3><p class="service__text">At vero eos et accusamus et iusto odio dignissimos ducimus qui</p></article>
        <article class="service"><svg class="service__icon" viewBox="0 0 28 28"><circle cx="14" cy="14" r="13" fill="none" stroke="#0a4f9e" stroke-width="1.2"/><circle cx="14" cy="14" r="11" fill="#1aa0e0"/><rect x="10" y="7" width="8" height="10" rx="2" fill="none" stroke="#fff" stroke-width="1"/><path d="M14 17v4" stroke="#fff" stroke-width="1"/></svg><h3 class="service__name">IV THERAPY</h3><p class="service__text">At vero eos et accusamus et iusto odio dignissimos ducimus qui</p></article>
      </div>
      <div class="dots" style="position:static;margin-top:21px"><i></i><i></i><i></i></div>
    </div>
  </section>

  <section class="block testimonials" style="--h:147px">
    <h2 class="section-title" style="padding-top:26px">TESTIMONIALS</h2>
    <span class="quote" style="left:42px;top:44px">“</span>
    <span class="quote" style="left:251px;top:98px">”</span>
    <div style="margin-top:8px"><div class="avatar" role="img" aria-label="Client portrait"></div></div>
    <p class="testimonial__text" style="margin-top:8px">Sed ut perspiciatis unde omnis iste natus error sit voluptatem accusantium doloremque laudantium, totam rem aperiam, eaque ipsa quae ab illo inventore veritatis et quasi architecto beatae vitae dicta sunt explicabo. Nemo enim ipsam voluptatem quia voluptas .</p>
    <p class="testimonial__author">-By Author Name</p>
    <span class="arrow" style="left:18px;top:84px">←</span>
    <span class="arrow" style="left:289px;top:84px">→</span>
  </section>

  <section class="block band blog" style="--h:165px">
    <div class="band__bg band__bg--blog" role="img" aria-label="Blue and teal backdrop of DNA strands"></div>
    <div class="band__inner" style="padding-top:12px">
      <h2 class="section-title section-title--light">LATEST &nbsp;BLOG</h2>
      <div class="posts" style="margin-top:11px">
        <article class="post"><div class="post__photo post__photo--1" role="img" aria-label="Gloved hand holding a blood sample tube"></div><div class="post__date"><span class="post__day">31</span><span class="post__month">J<br>U<br>L<br>Y</span></div><p class="post__by"><i></i>BY ADMIN</p><p class="post__text">At vero eos et accusamus et iusto odio dignissimos ducimus qui blanditiis praesentium .</p><span class="post__more">READ MORE</span></article>
        <article class="post"><div class="post__photo post__photo--2" role="img" aria-label="Laboratory microscope close-up"></div><div class="post__date"><span class="post__day">31</span><span class="post__month">J<br>U<br>L<br>Y</span></div><p class="post__by"><i></i>BY ADMIN</p><p class="post__text">At vero eos et accusamus et iusto odio dignissimos ducimus qui blanditiis praesentium .</p><span class="post__more">READ MORE</span></article>
        <article class="post"><div class="post__photo post__photo--3" role="img" aria-label="Therapist treating a patient's leg"></div><div class="post__date"><span class="post__day">31</span><span class="post__month">J<br>U<br>L<br>Y</span></div><p class="post__by"><i></i>BY ADMIN</p><p class="post__text">At vero eos et accusamus et iusto odio dignissimos ducimus qui blanditiis praesentium .</p><span class="post__more">READ MORE</span></article>
      </div>
      <div class="dots" style="position:static;margin-top:8px"><i></i><i class="on" style="background:#fff"></i></div>
    </div>
  </section>

  <section class="block newsletter" style="--h:109px">
    <h2 class="section-title" style="padding-top:22px">JOIN THE <em>NEWSLETTER</em></h2>
    <p class="newsletter__text">Sed ut perspiciatis unde omnis iste natus error sit voluptatem accusantium doloremque laudantium, totam rem aperiam, eaque ipsa quae ab illo inventore veritatis et quasi architecto.</p>
    <div class="subscribe"><div class="subscribe__field">Enter your Email<svg viewBox="0 0 12 10"><path d="M0 5L12 0 9 10 6 6Z" fill="#222"/></svg></div><span class="subscribe__btn">SUBMIT</span></div>
  </section>

  <footer class="block footer" style="--h:101px">
    <div class="brand" style="left:26px;top:17px"><span class="brand__dot"></span>LUMORA</div>
    <p class="footer__about" style="left:26px;top:40px">Lorem ipsum dolor sit amet, consectetur adipiscing elit, sed do eiusmod tempor incididunt ut labore et dolore magna aliqua. Ut enim ad minim veniam,</p>
    <div class="footer__col" style="left:120px;top:17px"><h4 class="footer__head">QUICKLINK</h4><ul class="footer__links"><li>HOME</li><li>ABOUTUS</li><li>SERVICES</li><li>BLOG</li><li>CONTACT US</li></ul></div>
    <div class="footer__col" style="left:173px;top:17px"><h4 class="footer__head">CONTACT US</h4><div class="footer__contact"><b>555-014-2200</b><br>info@lumora.com<br><span style="line-height:6px;display:block">12 Marrow Lane,<br>Avelon 20410</span></div></div>
    <div class="footer__col" style="left:247px;top:17px"><h4 class="footer__head">FOLLOW US</h4><div class="social"><i></i><i></i><i></i></div></div>
    <p class="footer__legal" style="bottom:9px">Copyrights © 2020 Copyrights Company Name | All Rights Reserved</p>
  </footer>
</main>

</body>
</html>
```